Business card design for Automotive workshop

We need a business card for a new automotive repair and tyre shop called Keelstone Prime Automotive located in New Zealand. We are a clean, modern and fresh workshop and company.

Front needs to feature logo,
my name:
Marlo Fenwicke (director)

Address:
48 Tarn Lane
Whitianga 3510

Phone: 07 594 2713
Mobile: 027 451 9362
Email: office@keelstoneautomotive.example.nz
Website: keelstoneautomotive.example.nz

Back needs to feature an area to write down appointment details, date and time.

Also feature a list of jobs and work we do such as,
Vehicle Servicing
All Mechanical Repairs
Warrant of Fitness
Tyres & Wheel Alignments
Automotive Diagnostics
Automotive Parts & Supplies

```html
<!DOCTYPE html>
<html lang="en">
<head>
<meta charset="utf-8">
<title>Keelstone Prime Automotive – Business Card</title>
<link rel="stylesheet" href="https://fonts.googleapis.com/css2?family=Open+Sans:wght@400;600;700&family=Roboto:wght@400;500;700&display=swap">
<style>
  :root {
    --page-bg: #d9d9db;
    --card-black: #1d1d1f;
    --brand-red: #e21d2b;
    --text-white: #f2f2f2;
    --text-grey: #9a9a9e;
    --logo-grey: #3a3a3d;
    --slip-white: #ffffff;
    --dot-grey: #777;
  }
  * { box-sizing: border-box; margin: 0; padding: 0; }
  html, body { width: 1200px; height: 960px; overflow: hidden; }
  body {
    background: var(--page-bg);
    position: relative;
    font-family: "Roboto", Arial, sans-serif;
  }
  .card {
    position: absolute;
    left: 250px;
    width: 700px;
    height: 400px;
    background: var(--card-black);
    overflow: hidden;
    box-shadow: 0 6px 18px rgba(0,0,0,.18);
  }
  .card--back { top: 60px; }
  .card--front { top: 500px; font-family: "Open Sans", Arial, sans-serif; }

  /* Back: wordmark + services + appointment slip */
  .wordmark {
    display: flex;
    align-items: center;
    justify-content: center;
    gap: 12px;
    font-family: "Roboto", Arial, sans-serif;
    font-weight: 700;
    letter-spacing: 2px;
    text-transform: uppercase;
  }
  .wordmark__square { width: 18px; height: 18px; background: var(--brand-red); }
  .card--back .wordmark {
    margin-top: 46px;
    font-size: 34px;
    color: var(--text-white);
  }
  .services { text-align: center; margin-top: 22px; }
  .services__headline {
    color: var(--brand-red);
    font-weight: 500;
    font-size: 19px;
    text-transform: uppercase;
    letter-spacing: .5px;
  }
  .services__list {
    color: var(--text-white);
    font-size: 15px;
    line-height: 22px;
    margin-top: 6px;
  }
  .services__bullet { color: var(--brand-red); margin: 0 6px; }
  .appointment {
    position: absolute;
    left: 36px; right: 36px; bottom: 36px;
    height: 112px;
    background: var(--slip-white);
    padding: 22px 28px;
    display: flex;
    flex-direction: column;
    justify-content: space-between;
  }
  .appointment__row { display: flex; align-items: flex-end; gap: 8px; }
  .appointment__label { color: var(--brand-red); font-weight: 500; font-size: 16px; }
  .appointment__line {
    flex: 1;
    border-bottom: 2px dotted var(--dot-grey);
    margin-bottom: 4px;
  }
  .appointment__line--date { flex: 1.4; margin-right: 14px; }

  /* Front: contact details */
  .card--front .wordmark {
    position: absolute;
    top: 78px; left: 0; right: 0;
    font-size: 32px;
    color: var(--logo-grey);
  }
  .card--front .wordmark__square { background: var(--logo-grey); }
  .contact {
    position: absolute;
    left: 56px; top: 196px;
    color: var(--text-white);
  }
  .contact__name {
    color: var(--brand-red);
    font-size: 24px;
    font-weight: 600;
    text-transform: uppercase;
    letter-spacing: .5px;
  }
  .contact__role { color: var(--text-grey); font-size: 16px; margin-top: -2px; }
  .contact__address { font-size: 16px; margin-top: 14px; }
  .contact__item {
    display: flex; align-items: center; gap: 10px;
    font-size: 16px; line-height: 24px;
  }
  .contact__icon { width: 14px; height: 14px; fill: var(--brand-red); flex: none; }
  .website {
    position: absolute;
    right: 40px; bottom: 54px;
    color: var(--text-white);
    font-size: 15px;
  }
  .stripe-white {
    position: absolute; left: 0; right: 0; bottom: 22px;
    height: 4px; background: var(--slip-white);
  }
  .stripe-red {
    position: absolute; left: 0; right: 0; bottom: 0;
    height: 14px; background: var(--brand-red);
  }
</style>
</head>
<body>

<section class="card card--back" aria-label="Card back: services and appointment">
  <div class="wordmark"><span class="wordmark__square"></span>Keelstone Prime Automotive</div>
  <div class="services">
    <p class="services__headline">Vehicle Servicing</p>
    <p class="services__list">All Mechanical Repairs<span class="services__bullet">•</span>Warrant of Fitness<span class="services__bullet">•</span>Tyres &amp; Wheel Alignments<br>
    Automotive Diagnostics<span class="services__bullet">•</span>Automotive Parts &amp; Supplies</p>
  </div>
  <div class="appointment">
    <div class="appointment__row">
      <span class="appointment__label">Date:</span><span class="appointment__line appointment__line--date"></span>
      <span class="appointment__label">Time:</span><span class="appointment__line"></span>
    </div>
    <div class="appointment__row">
      <span class="appointment__label">Date:</span><span class="appointment__line appointment__line--date"></span>
      <span class="appointment__label">Time:</span><span class="appointment__line"></span>
    </div>
  </div>
</section>

<section class="card card--front" aria-label="Card front: contact details">
  <div class="wordmark"><span class="wordmark__square"></span>Keelstone Prime Automotive</div>
  <div class="contact">
    <p class="contact__name">Marlo Fenwicke</p>
    <p class="contact__role">Director</p>
    <p class="contact__address">48 Tarn Lane Whitianga 3510</p>
    <p class="contact__item">
      <svg class="contact__icon" viewBox="0 0 24 24" aria-hidden="true"><path d="M6.6 10.8a15.1 15.1 0 0 0 6.6 6.6l2.2-2.2c.3-.3.7-.4 1-.2 1.1.4 2.3.6 3.6.6.6 0 1 .4 1 1V20c0 .6-.4 1-1 1A17 17 0 0 1 3 4c0-.6.4-1 1-1h3.5c.6 0 1 .4 1 1 0 1.3.2 2.5.6 3.6.1.3 0 .7-.2 1z"/></svg>
      07 594 2713
    </p>
    <p class="contact__item">
      <svg class="contact__icon" viewBox="0 0 24 24" aria-hidden="true"><path d="M7 1h10a2 2 0 0 1 2 2v18a2 2 0 0 1-2 2H7a2 2 0 0 1-2-2V3a2 2 0 0 1 2-2zm0 3v14h10V4zm5 15.5a1 1 0 1 0 0 2 1 1 0 0 0 0-2z"/></svg>
      027 451 9362
    </p>
    <p class="contact__item">
      <svg class="contact__icon" viewBox="0 0 24 24" aria-hidden="true"><path d="M2 5h20v14H2zm2 2v.5l8 5 8-5V7zm0 2.8V17h16V9.8l-8 5z"/></svg>
      office@keelstoneautomotive.example.nz
    </p>
  </div>
  <p class="website">www.keelstoneautomotive.example.nz</p>
  <div class="stripe-white"></div>
  <div class="stripe-red"></div>
</section>

</body>
</html>
```